Boutique custom software development company needs new business card

Our nearly 20 year old custom software development company would like to better include the fact that we are now providing Bitcoin services. These new services are B2B include education (how to acquire and securely hold Bitcoin) and integrating Bitcoin payments into existing ecommerce sites or other existing systems. Please keep the card clean and simple. Attached is our current design and some other files. vextorial.com

Target Market(s)

businesses owners interested in long term relationship

Industry/Entity Type

Custom software development and Bitcoin

Contact Information for Business Card

Dale Parker, dale@vextorial.com, vextorial.com, (888) 555-VXTRL

Font styles to use
Other font styles liked:
• monospace

Requirements
Must have
• double-sided
Nice to have
• clean and simple
Should not have
• physical address

```html
<!DOCTYPE html>
<html lang="en">
<head>
<meta charset="UTF-8">
<title>Vextorial Business Card</title>
<link href="https://fonts.googleapis.com/css2?family=Poppins:wght@400;500;700&display=swap" rel="stylesheet">
<style>
  :root {
    --stage: #1b1b1b;
    --card-white: #ffffff;
    --brand-blue: #3f73b8;
    --brand-orange: #f07b22;
    --ink: #333333;
    --soft-white: rgba(255, 255, 255, 0.88);
    --shadow: rgba(0, 0, 0, 0.9);
  }
  * { box-sizing: border-box; margin: 0; padding: 0; }
  html, body {
    width: 1075px;
    height: 1200px;
    overflow: hidden;
    background: var(--stage);
    font-family: "Poppins", sans-serif;
  }
  .card {
    position: absolute;
    left: 208px;
    width: 660px;
    height: 393px;
    border-radius: 26px;
    box-shadow: 3px 3px 0 var(--shadow);
    overflow: hidden;
  }
  .card--front { top: 188px; background: var(--card-white); }
  .card--back { top: 637px; background: var(--brand-blue); }

  .brand {
    position: absolute;
    right: 43px;
    top: 72px;
    text-align: right;
  }
  .brand__name {
    font-weight: 700;
    font-size: 46px;
    line-height: 1;
    letter-spacing: -1px;
    color: var(--brand-blue);
  }
  .brand__tagline {
    margin-top: 7px;
    font-size: 14.5px;
    letter-spacing: -0.3px;
    color: var(--brand-blue);
  }

  .holder {
    position: absolute;
    left: 39px;
    top: 199px;
    font-weight: 700;
    font-size: 27px;
    line-height: 1;
  }
  .holder__first { color: var(--brand-orange); }
  .holder__last { color: var(--brand-blue); }

  .divider {
    position: absolute;
    left: 39px;
    right: 43px;
    top: 241px;
    height: 2px;
    background: var(--brand-blue);
  }

  .contacts {
    position: absolute;
    left: 39px;
    top: 262px;
    list-style: none;
  }
  .contacts__item {
    display: flex;
    align-items: center;
    height: 29px;
    font-size: 19px;
    color: var(--ink);
  }
  .contacts__icon {
    width: 24px;
    height: 24px;
    border-radius: 3px;
    background: var(--brand-orange);
    margin-right: 9px;
    flex: none;
  }
  .contacts__highlight { color: var(--brand-blue); }

  .corner-mark {
    position: absolute;
    left: 0;
    bottom: 0;
    width: 118px;
    height: 118px;
    background: var(--brand-orange);
  }
  .back-services {
    position: absolute;
    right: 56px;
    top: 54px;
    text-align: right;
    color: var(--soft-white);
    font-size: 16px;
    font-weight: 500;
    line-height: 1.55;
    letter-spacing: 0.2px;
  }
  .back-services__item--accent { color: var(--card-white); font-weight: 700; }
  .back-brand {
    position: absolute;
    right: 56px;
    bottom: 36px;
    font-weight: 700;
    font-size: 62px;
    line-height: 1;
    letter-spacing: -1.5px;
    color: var(--card-white);
  }
</style>
</head>
<body>
  <section class="card card--front">
    <div class="brand">
      <div class="brand__name">VEXTORIAL</div>
      <div class="brand__tagline">custom applications &amp; bitcoin services</div>
    </div>

    <h1 class="holder"><span class="holder__first">DALE</span> <span class="holder__last">PARKER</span></h1>
    <div class="divider"></div>

    <ul class="contacts">
      <li class="contacts__item">
        <svg class="contacts__icon" viewBox="0 0 24 24" aria-hidden="true">
          <path d="M8 6.5c.6-.6 1.4-.5 1.8.1l1.1 1.7c.3.5.2 1.1-.2 1.5l-.8.7c.6 1.4 1.6 2.5 3 3.1l.7-.8c.4-.4 1-.5 1.5-.2l1.7 1.1c.6.4.7 1.2.1 1.8l-1 1c-.8.8-2 1-3 .5-2.8-1.3-4.9-3.4-6.2-6.2-.5-1-.3-2.2.5-3z" fill="#fff"/>
        </svg>
        (888) 555-VXTRL
      </li>
      <li class="contacts__item">
        <svg class="contacts__icon" viewBox="0 0 24 24" aria-hidden="true">
          <rect x="5" y="7" width="14" height="10" fill="none" stroke="#fff" stroke-width="1.5"/>
          <path d="M5 7l7 6 7-6" fill="none" stroke="#fff" stroke-width="1.5"/>
        </svg>
        dale@vextorial.com
      </li>
      <li class="contacts__item">
        <svg class="contacts__icon" viewBox="0 0 24 24" aria-hidden="true">
          <circle cx="12" cy="12" r="6.5" fill="none" stroke="#fff" stroke-width="1.4"/>
          <ellipse cx="12" cy="12" rx="2.8" ry="6.5" fill="none" stroke="#fff" stroke-width="1.2"/>
          <path d="M5.5 12h13M6.5 9h11M6.5 15h11" stroke="#fff" stroke-width="1.1"/>
        </svg>
        <span>www.<span class="contacts__highlight">vextorial</span>.com</span>
      </li>
    </ul>
  </section>

  <section class="card card--back">
    <div class="corner-mark" aria-hidden="true"></div>
    <div class="back-services">
      <div>Custom Software Development</div>
      <div class="back-services__item--accent">Bitcoin Education &amp; Payments</div>
    </div>
    <div class="back-brand">VEXTORIAL</div>
  </section>
</body>
</html>
```